Kelvaro.ch is looking for business card letterhead and envelope C5 with WOW effect

We need a strong business card for our company Kelvaro.ch, logo is available. You want a black or dark background on which the logo Stark r% 26 # 252; appears. Letterhead and envelope in C5 format should be in a similar design, but does not have to be We need a strong business card for our company Kelvaro.ch, logo is available. A black or dark background is desired, on which the logo Stark comes across. The letterhead and the envelope in C5 format should have a similar design.

Target Market(s)

Private customers as well as entrepreneurs

Contact Information for Business Card

E-mail: info@kelvaro-example.ch
Web.www.Kelvaro-example.ch
Tel: +41 ( 0 ) 79 482 6037
Adresse:
Lindenweg 14
9406 Tarnbach

Hier kann man Icons verwenden für Email,Tel und Adressse

Font styles to use
Other font styles liked:
• Dubai,bold

Colors

Designer to choose colors to be used in the design.

Requirements
Must have
• WOW effect
Nice to have
• R% 26 # 252; back business card with our service listings. - VEHICLE LABELING - SHOP WINDOW LABELING - STICKERS AND MUCH MORE ... in red color

```html
<!DOCTYPE html>
<html lang="en">
<head>
<meta charset="utf-8">
<title>Kelvaro.ch Business Card</title>
<link rel="stylesheet" href="https://fonts.googleapis.com/css2?family=Montserrat:wght@400;500;600&family=Saira:wght@600;700&display=swap">
<style>
  :root {
    --stage: #2a2a2c;
    --card-dark: #1c1c1e;
    --pattern-deep: #1a1a14;
    --pattern-olive: #3a3620;
    --accent: #f5c518;
    --text-light: #f2f2f2;
    --silver: #b9b9bb;
  }
  * { box-sizing: border-box; margin: 0; padding: 0; }
  html, body {
    width: 1200px; height: 874px; overflow: hidden;
    background: var(--stage);
    font-family: "Montserrat", Arial, sans-serif;
  }
  .canvas {
    position: relative; width: 1200px; height: 874px;
  }
  .card {
    position: absolute; left: 280px; width: 640px; height: 380px;
    overflow: hidden; box-shadow: 0 10px 30px rgba(0,0,0,.45);
  }
  .card--back { top: 42px; }
  .card--front { top: 452px; background: var(--card-dark); }

  .hex-field {
    position: absolute; inset: 0;
    background: radial-gradient(ellipse at 55% 45%, var(--pattern-olive) 0%, var(--pattern-deep) 80%);
  }
  .back-wordmark {
    position: absolute; left: 0; right: 0; top: 130px; text-align: center;
    font-family: "Montserrat", Arial, sans-serif; font-weight: 600;
    font-size: 54px; letter-spacing: 2px; color: var(--silver);
  }
  .service-list {
    position: absolute; left: 0; right: 0; bottom: 40px; text-align: center;
    font-size: 15px; font-weight: 500; letter-spacing: .5px; color: var(--accent);
  }

  .brand {
    position: absolute; left: 44px; top: 120px;
    display: flex; align-items: center; gap: 16px;
  }
  .brand-mark { width: 64px; height: 64px; background: var(--accent); }
  .brand-name {
    font-weight: 600; font-size: 30px; letter-spacing: 1px; color: var(--text-light);
  }
  .holder { position: absolute; left: 372px; top: 132px; }
  .holder-name {
    font-family: "Saira", Arial, sans-serif; font-weight: 700;
    font-size: 27px; line-height: 1; color: var(--accent);
  }
  .holder-role { font-size: 15px; color: var(--text-light); margin-top: 4px; }
  .contact-list { list-style: none; margin-top: 18px; }
  .contact-list li {
    display: flex; align-items: center; gap: 10px;
    font-size: 14.5px; color: var(--text-light); line-height: 24px;
  }
  .contact-list svg { width: 14px; height: 14px; fill: var(--accent); flex: none; }
  .address {
    position: absolute; left: 130px; bottom: 52px;
    display: flex; align-items: center; gap: 10px;
    font-size: 15px; color: var(--text-light);
  }
  .address svg { width: 13px; height: 16px; fill: var(--accent); }
</style>
</head>
<body>
<main class="canvas">

  <section class="card card--back">
    <div class="hex-field" role="img" aria-label="Dark olive honeycomb hexagon pattern"></div>
    <div class="back-wordmark">KELVARO.CH</div>
    <p class="service-list">VEHICLE LABELING • SHOP WINDOW LABELING • STICKERS</p>
  </section>

  <section class="card card--front">
    <div class="brand">
      <span class="brand-mark"></span>
      <span class="brand-name">KELVARO.CH</span>
    </div>

    <div class="holder">
      <h1 class="holder-name">Lukas Brenner</h1>
      <p class="holder-role">President</p>
      <ul class="contact-list">
        <li>
          <svg viewBox="0 0 24 24"><path d="M6.6 10.8a15.1 15.1 0 0 0 6.6 6.6l2.2-2.2a1 1 0 0 1 1-.25 11.4 11.4 0 0 0 3.6.57 1 1 0 0 1 1 1V20a1 1 0 0 1-1 1A17 17 0 0 1 3 4a1 1 0 0 1 1-1h3.5a1 1 0 0 1 1 1c0 1.25.2 2.45.57 3.6a1 1 0 0 1-.25 1z"/></svg>
          +41 ( 0 ) 79 482 6037
        </li>
        <li>
          <svg viewBox="0 0 24 24"><path d="M2 5h20v14H2z M2 5l10 8 10-8" /><path d="M2 5h20L12 12.5z" fill="#1c1c1e"/></svg>
          info@kelvaro-example.ch
        </li>
        <li>
          <svg viewBox="0 0 24 24"><path d="M12 2a10 10 0 1 0 0 20 10 10 0 0 0 0-20zm6.9 6h-3a15.6 15.6 0 0 0-1.4-3.6A8 8 0 0 1 18.9 8zM12 4a14 14 0 0 1 1.9 4h-3.8A14 14 0 0 1 12 4zM4.3 14a8 8 0 0 1 0-4h3.4a16 16 0 0 0 0 4zm.8 2h3a15.6 15.6 0 0 0 1.4 3.6A8 8 0 0 1 5.1 16zm3-8h-3a8 8 0 0 1 4.4-3.6A15.6 15.6 0 0 0 8.1 8zM12 20a14 14 0 0 1-1.9-4h3.8A14 14 0 0 1 12 20zm2.3-6H9.7a14.7 14.7 0 0 1 0-4h4.6a14.7 14.7 0 0 1 0 4zm.2 5.6A15.6 15.6 0 0 0 15.9 16h3a8 8 0 0 1-4.4 3.6zM16.3 14a16 16 0 0 0 0-4h3.4a8 8 0 0 1 0 4z"/></svg>
          www.Kelvaro-example.ch
        </li>
      </ul>
    </div>

    <p class="address">
      <svg viewBox="0 0 24 30"><path d="M12 0a12 12 0 0 0-12 12c0 9 12 18 12 18s12-9 12-18A12 12 0 0 0 12 0zm0 17a5 5 0 1 1 0-10 5 5 0 0 1 0 10z"/></svg>
      Lindenweg 14 9406 Tarnbach
    </p>
  </section>

</main>
</body>
</html>
```